R7M Horizon Business Card Design

We need a business card created for our New Business "R7M Horizon"<br/><br/>The business card design is up to you however the following information must be on the business card:<br/><br/>Front of the business card -<br/>Email :darrenp@r7mhorizon.nz<br/>Mobile: +64 (0) 22 4870 619<br/>Website: www.r7mhorizon.nz<br/>Card Owner Name: Darren Paltrow<br/>Company Title: Business Development Manager<br/>Slogan: "Bold ideas, clear horizons". <br/>Logo On the front attached to the design brief<br/><br/>On the back: <br/>Space on the back for 4 more versions of the logo across the bottom of the card indicating different subsidiary brands - R7M Coffee, R7M Arts, R7M ?? (The card will be used for all of these brands - We Will add the extra subsidiary logos to the design once the design is finished (We are a graphics design team). <br/><br/>Other than that we want a premium feeling logo that remains universally usable depending on the business entity that we are using the card for. The use of bright bold colours would be great but we still want the card to feel premium.
Target Market(s)
Gift Design and Manufacturing Companies
Contact Information for Business Card
Front of the business card -
Email :darrenp@r7mhorizon.nz
Mobile: +64 (0) 22 4870 619
Website: www.r7mhorizon.nz
Card Owner Name: Darren Paltrow
Company Title: Business Development Manager
Slogan: "Bold ideas, clear horizons".
Logo On the front attached to the design brief

```html
<!DOCTYPE html>
<html lang="en">
<head>
<meta charset="utf-8">
<title>R7M Horizon Business Card</title>
<link rel="stylesheet" href="https://fonts.googleapis.com/css2?family=Exo+2:ital,wght@0,400;0,600;0,700;1,600&family=Titillium+Web:wght@400;600&display=swap">
<style>
  :root {
    --backdrop: #1c1c1e;
    --card: #27282a;
    --card-deep: #222325;
    --accent: #3b4fc4;
    --accent-faint: rgba(59, 79, 196, 0.28);
    --ink: #f2f2f4;
    --emboss: #34353a;
  }
  * { margin: 0; padding: 0; box-sizing: border-box; }
  html, body {
    width: 1200px; height: 900px; overflow: hidden;
    background: radial-gradient(ellipse at 50% 40%, #2b2b2e 0%, var(--backdrop) 70%);
  }
  .canvas { position: relative; width: 1200px; height: 900px; }
  .card {
    position: absolute; left: 250px; width: 700px; height: 380px;
    background: var(--card);
    border-left: 3px solid var(--accent);
    border-bottom: 3px solid var(--accent);
    box-shadow: 0 14px 30px rgba(0, 0, 0, 0.55);
    overflow: hidden;
  }
  .card--back { top: 50px; background: var(--card-deep); }
  .card--front { top: 470px; }

  .back-ring {
    position: absolute; left: 50%; top: 50%;
    width: 300px; height: 300px; margin: -150px 0 0 -150px;
    border: 5px solid var(--accent-faint); border-radius: 50%;
  }
  .back-name {
    position: absolute; left: 0; right: 0; top: 165px; text-align: center;
    font: 600 42px/1 "Exo 2", sans-serif; color: var(--emboss);
    letter-spacing: 1px;
  }

  .brand {
    position: absolute; left: 0; right: 0; top: 50px; text-align: center;
    font: 600 44px/1 "Exo 2", sans-serif; color: var(--accent);
    letter-spacing: 1px;
  }
  .divider {
    position: absolute; left: 90px; width: 570px; top: 130px;
    height: 1.5px; background: var(--accent);
  }
  .divider--short {
    left: 400px; top: 180px; width: 1.5px; height: 80px;
  }
  .owner { position: absolute; left: 60px; top: 180px; text-align: right; width: 320px; }
  .owner__name {
    font: 700 26px/1.15 "Exo 2", sans-serif; color: var(--accent);
    text-transform: uppercase; letter-spacing: 0.5px;
  }
  .owner__role {
    font: 400 19px/1.3 "Titillium Web", sans-serif; color: var(--ink);
  }
  .contacts { position: absolute; left: 425px; top: 190px; list-style: none; }
  .contacts li {
    display: flex; align-items: center; gap: 10px;
    font: 400 19px/1.45 "Titillium Web", sans-serif; color: var(--ink);
    white-space: nowrap;
  }
  .contacts svg { width: 18px; height: 18px; flex: none; }
  .slogan {
    position: absolute; left: 0; right: 0; top: 318px; text-align: center;
    font: 400 22px/1 "Titillium Web", sans-serif; color: var(--accent);
  }
</style>
</head>
<body>
<main class="canvas">
  <section class="card card--back" aria-label="Card back">
    <div class="back-ring"></div>
    <p class="back-name">R7M Horizon</p>
  </section>

  <section class="card card--front" aria-label="Card front">
    <p class="brand">R7M Horizon</p>
    <div class="divider"></div>
    <div class="divider divider--short"></div>
    <div class="owner">
      <p class="owner__name">Darren Paltrow</p>
      <p class="owner__role">Business Development Manager</p>
    </div>
    <ul class="contacts">
      <li>
        <svg viewBox="0 0 20 20" fill="none" stroke="#3b4fc4" stroke-width="1.6"><circle cx="10" cy="10" r="8.5"/><path d="M7 5.5l1.8 2.6-1 1.2c.7 1.4 1.6 2.3 3 3l1.2-1 2.5 1.8-.9 1.6c-3.6-.3-7-3.7-7.3-7.3z"/></svg>
        +64 (0) 22 4870 619
      </li>
      <li>
        <svg viewBox="0 0 20 20" fill="none" stroke="#3b4fc4" stroke-width="1.6"><rect x="2" y="4.5" width="16" height="11" rx="1"/><path d="M2.5 5l7.5 6 7.5-6"/></svg>
        darrenp@r7mhorizon.nz
      </li>
      <li>
        <svg viewBox="0 0 20 20" fill="none" stroke="#3b4fc4" stroke-width="1.6"><circle cx="10" cy="10" r="8"/><ellipse cx="10" cy="10" rx="3.5" ry="8"/><path d="M2 10h16M3.5 6h13M3.5 14h13"/></svg>
        www.r7mhorizon.nz
      </li>
    </ul>
    <p class="slogan">Bold ideas, clear horizons</p>
  </section>
</main>
</body>
</html>
```